Stationery Design Task - Stationary, memo and report templates for professional services company

Looking for someone to update stationary design but just as importantly come up with a template for reports and memos for use in our consulting firm. Would also like some brand use guidelines to be able to share with our whole team. We have an existing logo that we like. Need to update with a more contemporary look so that our deliverables to clients look good and professional yet stylish. This is for business to business communications. No need for envelope design. Important to have design for multiple pages, i.e. first page of a report and then 2nd page. Need to use in MS word documents so must be easy to use and replicate. Don't want something overly complex. Clean, fresh looking is best.

Industry/Entity Type

Information Technology

Font styles to use
Sans Serif

Colors
33a6d7
0792cd
85cae6
cee9f5
cedeed
85abd2
3377b5
0455a3

Requirements
Must have
• Clean look but with a little style or pop. Something that can easily be used in word documents. Need to have page styles that have a first page of a report (not a cover page) and then secondary page.
Nice to have
• - Although the dark blue is our primary color. Might be willing to look at some accent color as well.
Should not have
• Not just our logo on the page with a color bar.

```html
<!DOCTYPE html>
<html lang="en">
<head>
<meta charset="utf-8">
<title>Nexora Systems Stationery</title>
<link rel="stylesheet" href="https://fonts.googleapis.com/css2?family=Roboto:wght@400;700;900&family=Questrial&display=swap">
<style>
  :root {
    --board: #666666;
    --brand-blue: #0b7bc4;
    --bright-blue: #0792cd;
    --sky-blue: #33a6d7;
    --pale-blue: #85cae6;
    --ink-grey: #5f5f60;
    --body-grey: #555555;
    --page-top: #ffffff;
    --page-bottom: #c9c9ca;
    --faint-mark: rgba(200, 200, 200, 0.2);
  }
  * { margin: 0; padding: 0; box-sizing: border-box; }
  html, body { width: 1200px; height: 578px; overflow: hidden; }
  body { background: var(--board); position: relative; font-family: "Questrial", sans-serif; }

  .sheet {
    position: absolute; top: 52px; width: 339px; height: 476px; overflow: hidden;
    box-shadow: 0 1px 4px rgba(0,0,0,0.3);
  }
  .sheet--cover { left: 61px; background: linear-gradient(180deg, var(--page-top) 0%, #e6e6e7 45%, var(--page-bottom) 100%); }
  .sheet--letter { left: 434px; background: linear-gradient(180deg, var(--page-top) 0%, #f2f2f2 60%, #dcdcdd 100%); }
  .sheet--continuation { left: 806px; background: linear-gradient(90deg, #d4d4d5 0%, #f4f4f4 35%, #ffffff 70%, #f6f6f6 100%); }

  .brand-name {
    position: absolute; display: flex; align-items: center;
    font-family: "Roboto", sans-serif; font-weight: 700; color: var(--brand-blue);
    white-space: nowrap; letter-spacing: 0.3px;
  }
  .brand-name__dot { display: block; flex: none; border-radius: 50%; background: var(--brand-blue); }

  /* Cover */
  .cover-band { position: absolute; left: 8px; top: 14px; width: 112px; height: 446px; }
  .cover-brand { left: 114px; top: 46px; font-size: 17px; gap: 7px; }
  .cover-brand .brand-name__dot { width: 28px; height: 28px; }
  .report-title {
    position: absolute; left: 82px; width: 260px; top: 184px;
    font-family: "Roboto", sans-serif; font-weight: 900; font-size: 32px; line-height: 0.98;
    color: var(--ink-grey); text-align: center; text-transform: uppercase; white-space: nowrap;
  }
  .prepared-block {
    position: absolute; left: 137px; width: 141px; top: 302px; height: 37px;
    border-top: 1px solid var(--ink-grey); border-bottom: 1px solid var(--ink-grey);
    text-align: center; font-family: "Roboto", sans-serif; font-weight: 700; white-space: nowrap;
  }
  .prepared-block__label { font-size: 11.5px; color: var(--ink-grey); margin-top: 5px; letter-spacing: 0.2px; }
  .prepared-block__name { font-size: 10px; color: var(--bright-blue); margin-top: 3px; font-weight: 400; letter-spacing: 0.3px; }
  .proposal-date { position: absolute; text-align: center; font-family: "Roboto", sans-serif; white-space: nowrap; }
  .proposal-date__label { font-size: 8px; color: var(--bright-blue); letter-spacing: 0.2px; }
  .proposal-date__value { font-size: 8px; color: #333; margin-top: 1px; }
  .proposal-date--issued { left: 52px; top: 434px; width: 90px; }
  .proposal-date--valid { left: 224px; top: 432px; width: 90px; }

  /* Letter */
  .letter-mark { position: absolute; left: 100px; top: 140px; width: 220px; height: 220px; border-radius: 50%; background: var(--faint-mark); }
  .letter-brand { left: 84px; top: 35px; font-size: 15px; gap: 6px; }
  .letter-brand .brand-name__dot { width: 23px; height: 23px; }
  .letter-body { position: absolute; left: 30px; top: 133px; width: 293px; color: var(--body-grey); }
  .letter-body__greeting { font-size: 8.5px; margin-bottom: 13px; color: #444; }
  .letter-body p { font-size: 4.7px; line-height: 7.3px; margin-bottom: 6.5px; text-align: justify; }
  .letter-body__closing { font-size: 4.7px; margin-top: 10px; }
  .letter-signature {
    position: absolute; left: 26px; top: 332px; width: 64px; height: 26px;
    background: linear-gradient(90deg, rgba(51,119,181,0.15), rgba(51,119,181,0.05));
    border-radius: 3px;
  }
  .letter-footer-band { position: absolute; left: 10px; top: 406px; width: 317px; height: 39px; }
  .letter-contact {
    position: absolute; left: 10px; top: 445px; width: 317px; height: 15px;
    background: var(--bright-blue); color: #fff;
    font-family: "Roboto", sans-serif; font-weight: 700; font-size: 5.4px; white-space: nowrap;
    display: flex; align-items: center; justify-content: center; gap: 10px; letter-spacing: 0.1px;
  }
  .letter-web {
    position: absolute; left: 0; width: 100%; top: 464px; text-align: center;
    font-size: 5.2px; letter-spacing: 1.3px; color: var(--sky-blue);
  }

  /* Continuation */
  .continuation-mark { position: absolute; left: 46px; top: 132px; width: 240px; height: 240px; border-radius: 50%; background: var(--faint-mark); }
  .continuation-dot { position: absolute; left: 293px; top: 422px; width: 30px; height: 30px; border-radius: 50%; background: var(--brand-blue); }
</style>
</head>
<body>

  <section class="sheet sheet--cover" aria-label="Report cover page">
    <svg class="cover-band" viewBox="0 0 112 446" role="img" aria-label="Blue hexagon pattern band along the left edge">
      <defs>
        <linearGradient id="coverBandFill" x1="0" y1="0" x2="1" y2="1">
          <stop offset="0" stop-color="#0792cd"/>
          <stop offset="1" stop-color="#0b6fb8"/>
        </linearGradient>
      </defs>
      <path d="M0 0 L20 0 L48 40 L70 90 L92 150 L108 230 L104 300 L88 360 L60 410 L30 446 L0 446 Z" fill="url(#coverBandFill)"/>
    </svg>
    <div class="brand-name cover-brand"><span class="brand-name__dot"></span>NEXORA SYSTEMS</div>
    <h1 class="report-title">Report<br>Title Here</h1>
    <div class="prepared-block">
      <div class="prepared-block__label">REPORT PREPARED BY</div>
      <div class="prepared-block__name">YOUR NAME HERE</div>
    </div>
    <div class="proposal-date proposal-date--issued">
      <div class="proposal-date__label">PROPOSAL ISSUED</div>
      <div class="proposal-date__value">SEP 19,2018</div>
    </div>
    <div class="proposal-date proposal-date--valid">
      <div class="proposal-date__label">PROPOSAL VALID TO</div>
      <div class="proposal-date__value">SEP 19,2019</div>
    </div>
  </section>

  <section class="sheet sheet--letter" aria-label="Letterhead page">
    <div class="letter-mark"></div>
    <div class="brand-name letter-brand"><span class="brand-name__dot"></span>NEXORA SYSTEMS</div>
    <div class="letter-body">
      <div class="letter-body__greeting">Dear Mr. Carter,</div>
      <p>Thank you for meeting with our team last week to discuss the planned upgrade of your network services. As promised, this letter outlines the scope we reviewed together, the main phases of the work and the support we will provide once the new systems are in place across all of your regional offices.</p>
      <p>The first phase covers an audit of current hardware, licences and security settings. Our engineers will then prepare a migration plan with clear milestones, so your staff know exactly when each change happens. We expect minimal downtime, and all work on core systems will be scheduled outside normal business hours.</p>
      <p>In the second phase we will move your data to the new platform, test every connection and train key users on the updated tools. A dedicated project lead will report progress each week and flag any risks early. After launch, our help desk remains available for questions, fixes and routine maintenance requests.</p>
      <p>We have attached a full proposal with costs and timelines for your review. Please let us know if you would like to adjust any part of the plan before we begin. We look forward to working with you.</p>
      <div class="letter-body__closing">Sincerely,</div>
    </div>
    <div class="letter-signature" role="img" aria-label="Handwritten signature of Paul Carter"></div>
    <svg class="letter-footer-band" viewBox="0 0 317 39" role="img" aria-label="Blue hexagon pattern band above the footer">
      <defs>
        <linearGradient id="letterBandFill" x1="0" y1="0" x2="1" y2="0">
          <stop offset="0" stop-color="#85cae6"/>
          <stop offset="0.5" stop-color="#33a6d7"/>
          <stop offset="1" stop-color="#0792cd"/>
        </linearGradient>
      </defs>
      <path d="M0 8 L120 20 L200 4 L317 0 L317 39 L0 39 Z" fill="url(#letterBandFill)"/>
    </svg>
    <div class="letter-contact">
      <span>2140 HARBOR ROW, JUNEAU, ALASKA 34210</span>
      <span>512 660 1847 | INFO@NEXORASYSTEMS.COM</span>
    </div>
    <div class="letter-web">www.nexorasystems.com</div>
  </section>

  <section class="sheet sheet--continuation" aria-label="Continuation page">
    <div class="continuation-mark"></div>
    <div class="continuation-dot"></div>
  </section>

</body>
</html>
```